Clear Coat 5L & 2.5L kit

Clear coat 5 Liter with 2.5 Liter hardener
I attached few examples
Required size:
5L
Actual size is: 22.875 x 10.4375 inch
With bleed added: 23.125 x 10.6875 inch
2.5L
Actual size is: 22.875 x 6.1875 inch
With bleed added: 23.125x6.2125 inch

Thanks

```html
<!DOCTYPE html>
<html lang="en">
<head>
<meta charset="utf-8">
<title>Halvex Finish – Ultra Clear Coat 5L &amp; Hardener 2.5L labels</title>
<link href="https://fonts.googleapis.com/css2?family=Lexend:wght@300;400;700&family=Barlow+Condensed:wght@400;600&family=Archivo+Narrow:wght@400;700&display=swap" rel="stylesheet">
<style>
  :root{
    --yellow:#fcd307;
    --black:#141414;
    --red:#e8262b;
    --white:#ffffff;
    --muted:#d9c26a;
    --page:#ffffff;
  }
  *{box-sizing:border-box;margin:0;padding:0}
  html,body{width:1200px;height:1038px;overflow:hidden;background:var(--page)}
  body{position:relative;font-family:"Archivo Narrow",Arial,sans-serif;color:var(--black)}

  .label{position:absolute;background:var(--yellow);overflow:hidden;box-shadow:0 2px 6px rgba(0,0,0,.18)}
  .label--clear{left:40px;top:76px;width:1112px;height:508px}
  .label--hardener{left:38px;top:634px;width:1114px;height:300px}
  .band{position:absolute;left:0;right:0;bottom:0;background:var(--black)}
  .label--clear .band{top:382px}
  .label--hardener .band{top:217px}

  .abs{position:absolute}
  .dot{position:absolute;width:11px;height:11px;border:1.6px solid var(--red);border-radius:50%}
  .dot--on::after{content:"";position:absolute;left:2px;top:2px;width:4px;height:4px;border-radius:50%;background:var(--red)}

  .side-title{position:absolute;transform:rotate(-90deg);transform-origin:left top;font-family:"Lexend",sans-serif;font-weight:300;color:var(--black);white-space:nowrap;letter-spacing:.2px}
  .side-title b{font-weight:700}

  .brand{position:absolute;font-family:"Lexend",sans-serif;font-weight:700;color:var(--black);line-height:.95;letter-spacing:-1px}
  .brand span{display:block}
  .brand__mark{position:absolute;border-radius:50%;background:var(--red)}

  .product{position:absolute;font-family:"Lexend",sans-serif;color:var(--black);line-height:1}
  .product__ultra{font-weight:300}
  .product__name{font-weight:700;letter-spacing:.5px}
  .product__voc{font-family:"Barlow Condensed",sans-serif;font-weight:600}
  .badge-slow{display:inline-block;background:var(--black);color:var(--red);font-family:"Lexend",sans-serif;font-weight:700;padding:1px 6px;letter-spacing:.5px}

  .volume{position:absolute;font-family:"Lexend",sans-serif;font-weight:700;color:var(--yellow);line-height:1}
  .features{position:absolute;list-style:none;font-family:"Barlow Condensed",sans-serif;color:var(--yellow)}
  .features li{position:relative;padding-left:22px}
  .features li .dot{left:0;top:50%;margin-top:-6px}
  .features .mix{font-weight:600;letter-spacing:.5px}

  .fine{position:absolute;color:var(--black);line-height:1.24}
  .fine h4{font-weight:700;font-size:inherit;text-transform:uppercase}
  .fine p{margin-bottom:.9em}
  .fine .caps{font-weight:700;text-transform:uppercase}

  .company{position:absolute;color:var(--yellow);line-height:1.3}
  .company strong{font-weight:700}
  .liters{position:absolute;transform:rotate(-90deg);transform-origin:left top;font-family:"Lexend",sans-serif;font-weight:700;color:var(--yellow);white-space:nowrap}
  .reach{position:absolute;color:var(--muted);line-height:1.3}
  .reach h5{color:var(--yellow);font-weight:700;font-size:inherit}

  .danger{position:absolute;border:1px solid var(--muted);text-align:center}
  .danger__title{position:absolute;left:50%;transform:translateX(-50%);background:var(--black);color:var(--yellow);font-family:"Barlow Condensed",sans-serif;font-weight:600;padding:0 5px;white-space:nowrap}
  .danger__icons{position:absolute;left:0;right:0;display:flex;justify-content:center}
  .danger__icons svg{display:block}
</style>
</head>
<body>
<svg width="0" height="0" style="position:absolute" aria-hidden="true">
  <defs>
    <symbol id="icon-flame" viewBox="0 0 24 24"><circle cx="12" cy="12" r="11" fill="#fff" stroke="#e8262b" stroke-width="1.5"/><path d="M12 4c1 3 5 5 5 10a5 5 0 0 1-10 0c0-2 1-3 2-4 0 2 1 3 2 3-1-3 0-6 1-9z" fill="#141414"/></symbol>
    <symbol id="icon-alert" viewBox="0 0 24 24"><circle cx="12" cy="12" r="11" fill="#fff" stroke="#e8262b" stroke-width="1.5"/><path d="M12 5l7 13H5z" fill="none" stroke="#141414" stroke-width="1.8" stroke-linejoin="round"/><path d="M12 10v4" stroke="#141414" stroke-width="1.8"/><circle cx="12" cy="16.3" r="1" fill="#141414"/></symbol>
    <symbol id="icon-health" viewBox="0 0 24 24"><circle cx="12" cy="12" r="11" fill="#fff" stroke="#e8262b" stroke-width="1.5"/><path d="M10 5h4v5h5v4h-5v5h-4v-5H5v-4h5z" fill="#141414"/></symbol>
  </defs>
</svg>

<!-- ===== 5L clear coat label ===== -->
<section class="label label--clear" aria-label="Ultra Clear Coat 5 litre label">
  <div class="band"></div>

  <div class="side-title" style="left:18px;top:194px;font-size:14px">ULTRA <b>CLEAR COAT</b></div>
  <span class="dot" style="left:23px;top:31px"></span>
  <span class="dot" style="left:23px;top:55px"></span>
  <span class="dot" style="left:23px;top:223px"></span>
  <span class="dot" style="left:23px;top:247px"></span>
  <span class="dot dot--on" style="left:23px;top:271px"></span>
  <span class="dot dot--on" style="left:23px;top:295px"></span>
  <span class="dot dot--on" style="left:23px;top:319px"></span>
  <span class="dot dot--on" style="left:23px;top:343px"></span>
  <span class="dot" style="left:23px;top:367px"></span>

  <div class="brand" style="left:216px;top:84px;font-size:76px">
    <span>HALVEX</span><span style="font-size:40px;letter-spacing:4px;margin-top:8px">FINISH</span>
  </div>
  <span class="brand__mark" style="left:518px;top:104px;width:18px;height:18px"></span>

  <div class="product" style="left:219px;top:222px">
    <div class="product__ultra" style="font-size:23px">ULTRA</div>
    <div class="product__name" style="font-size:38px;margin-top:6px">CLEAR COAT</div>
    <div class="product__voc" style="font-size:18px;margin-top:6px;margin-left:3px">VOC 2.1</div>
  </div>

  <span class="dot" style="left:355px;top:340px"></span>
  <span class="dot" style="left:355px;top:364px"></span>
  <ul class="features" style="left:355px;top:386px;font-size:15px;line-height:23.6px">
    <li><span class="dot dot--on"></span>High Gloss</li>
    <li><span class="dot dot--on"></span>Good Leveling</li>
    <li><span class="dot dot--on"></span>Easy Application</li>
    <li class="mix"><span class="dot dot--on"></span>2:1 MIX</li>
  </ul>
  <span class="dot" style="left:355px;top:485px"></span>

  <div class="volume" style="left:218px;top:430px;font-size:56px">5L</div>

  <!-- middle panel -->
  <div class="brand" style="left:540px;top:48px;font-size:29px;letter-spacing:-.5px">
    <span>HALVEX</span><span style="font-size:15px;letter-spacing:2px;margin-top:2px">FINISH</span>
  </div>
  <div class="fine" style="left:540px;top:124px;width:142px;font-size:5.6px">
    <p class="caps">For use only by professionals<br>Not for sale or use by general public</p>
    <h4>Notice to purchaser - <span style="text-transform:none">Limited Warranty.</span></h4>
    <p>Seller warrants this product is made to its stated specification. Results depend on surface preparation, mixing ratio, film build and curing conditions beyond our control. Buyer accepts all risk of use. Liability is limited to replacement of product proven defective.</p>
    <h4>Warning!</h4>
    <p class="caps">Contains isocyanates and flammable solvents. Read the safety data sheet before use. Wear an approved respirator, gloves and eye protection. Use only with adequate ventilation. Keep container closed when not in use.</p>
    <h4>Warranty:</h4>
    <p>This product is guaranteed to be free from defects when stored and applied as directed. Store between 5 and 30 °C away from heat and open flame. Shelf life is twelve months in the unopened original container. Do not mix with products of other systems. Claims must include the batch number printed on the can.</p>
  </div>

  <!-- right panel -->
  <div class="brand" style="left:894px;top:48px;font-size:29px;letter-spacing:-.5px">
    <span>HALVEX</span><span style="font-size:15px;letter-spacing:2px;margin-top:2px">FINISH</span>
  </div>
  <div class="fine" style="left:740px;top:120px;width:262px;font-size:5.6px">
    <h4>Description:</h4>
    <p>A two component high solids urethane clear for automotive refinishing. Delivers deep gloss, excellent flow and leveling, and strong resistance to weather, fuel and UV exposure. Mix 2 parts clear with 1 part hardener. Apply two medium wet coats with 5 to 10 minutes flash between coats. Air dry overnight or bake 30 minutes at 60 °C.</p>
    <h4>Warning! Flammable, vapor and spray mist harmful. May cause lung irritation and allergic respiration reaction</h4>
    <p style="margin-bottom:0">Keep away from heat, sparks and open flame. Vapors may travel to a source of ignition and flash back. Breathing vapor or spray mist may cause allergic reaction, asthma-like symptoms and lung damage. Persons with respiratory allergies must not work with this product. Avoid contact with skin and eyes.</p>
    <p><b>NIOSH/MSHA</b> approved air-supplied respirator is recommended during spraying. If one is not available, use a properly fitted organic vapor cartridge respirator with particulate prefilter. Ground all equipment. Use explosion-proof ventilation. Dispose of waste and empty containers according to local regulations.</p>
    <h4>First aid:</h4>
    <p>If inhaled, move to fresh air and call a physician if breathing is difficult. On skin contact, wash thoroughly with soap and water. In case of eye contact, flush with water for at least 15 minutes and get medical attention. If swallowed, do not induce vomiting; call a poison control center at once.</p>
    <h4>Notice:</h4>
    <p>Contents are for industrial use only. Product data is believed accurate but is given without warranty. Always test for compatibility before full application.</p>
  </div>

  <div class="company" style="left:540px;top:436px;font-size:6.6px">
    <strong>Halvex Finish, Inc.</strong><br>240 Harlow Park Rd,<br>Ashford, CA 90210<br>(800) 555-0147
    <div style="margin-top:12px"><strong>Made in EU</strong></div>
  </div>
  <div class="liters" style="left:652px;top:492px;font-size:17px">5 LITERS</div>

  <div class="reach" style="left:740px;top:436px;width:142px;font-size:6px">
    <h5>KEEP OUT OF THE REACH OF CHILDREN</h5>
    <p style="margin-top:8px">Do not store above 30 °C. Keep container tightly closed in a dry, well ventilated place. Contents under no pressure; open slowly.</p>
  </div>
  <div class="danger" style="left:896px;top:442px;width:100px;height:50px">
    <div class="danger__title" style="top:-9px;font-size:16px">DANGER</div>
    <div class="danger__icons" style="top:17px;gap:6px">
      <svg width="23" height="23"><use href="#icon-flame"/></svg>
      <svg width="23" height="23"><use href="#icon-health"/></svg>
      <svg width="23" height="23"><use href="#icon-alert"/></svg>
    </div>
  </div>
</section>

<!-- ===== 2.5L hardener label ===== -->
<section class="label label--hardener" aria-label="Ultra Hardener 2.5 litre label">
  <div class="band"></div>

  <div class="side-title" style="left:19px;top:148px;font-size:12px">ULTRA <b>HARDENER</b></div>
  <span class="dot" style="left:27px;top:13px"></span>
  <span class="dot" style="left:27px;top:154px"></span>
  <span class="dot dot--on" style="left:27px;top:178px"></span>
  <span class="dot dot--on" style="left:27px;top:202px"></span>
  <span class="dot" style="left:27px;top:226px"></span>

  <div class="brand" style="left:258px;top:32px;font-size:52px">
    <span>HALVEX</span><span style="font-size:27px;letter-spacing:3px;margin-top:5px">FINISH</span>
  </div>
  <span class="brand__mark" style="left:466px;top:46px;width:13px;height:13px"></span>

  <div class="product" style="left:258px;top:115px">
    <div class="product__ultra" style="font-size:15px">ULTRA</div>
    <div class="product__name" style="font-size:19px;margin-top:3px;letter-spacing:1px">HARDENER<br>FOR CLEAR COAT</div>
    <div class="product__voc" style="font-size:11px;margin-top:2px;display:flex;justify-content:space-between;width:163px">VOC 2.1 <span class="badge-slow" style="font-size:9px">SLOW</span></div>
  </div>

  <span class="dot" style="left:354px;top:201px"></span>
  <span class="dot" style="left:354px;top:225px"></span>
  <span class="dot" style="left:354px;top:249px"></span>
  <ul class="features" style="left:354px;top:264px;font-size:13px;line-height:20px">
    <li class="mix"><span class="dot dot--on"></span>2:1 MIX</li>
  </ul>

  <div class="volume" style="left:258px;top:259px;font-size:23px">2.5L</div>

  <div class="fine" style="left:543px;top:18px;width:140px;font-size:4.5px">
    <p class="caps" style="font-size:5px">For use only by professionals<br>Not for sale or use by general public</p>
    <h4>Notice to purchaser - <span style="text-transform:none">Limited Warranty.</span></h4>
    <p>Seller warrants this product is made to its stated specification. Results depend on surface preparation, mixing ratio, film build and curing conditions beyond our control. Buyer accepts all risk of use. Liability is limited to replacement of product proven defective.</p>
    <h4>Warning!</h4>
    <p class="caps">Contains isocyanates and flammable solvents. Read the safety data sheet before use. Wear an approved respirator, gloves and eye protection. Use only with adequate ventilation. Keep container closed when not in use.</p>
    <h4>Warranty:</h4>
    <p>This product is guaranteed to be free from defects when stored and applied as directed. Store between 5 and 30 °C away from heat and open flame. Shelf life is twelve months in the unopened original container. Do not mix with products of other systems. Claims must include the batch number printed on the can.</p>
  </div>

  <div class="fine" style="left:750px;top:20px;width:242px;font-size:4.4px">
    <h4>Description:</h4>
    <p>A two component high solids urethane clear for automotive refinishing. Delivers deep gloss, excellent flow and leveling, and strong resistance to weather, fuel and UV exposure. Mix 2 parts clear with 1 part hardener. Apply two medium wet coats with 5 to 10 minutes flash between coats. Air dry overnight or bake 30 minutes at 60 °C.</p>
    <h4>Warning! Flammable, vapor and spray mist harmful. May cause lung irritation and allergic respiration reaction</h4>
    <p style="margin-bottom:0">Keep away from heat, sparks and open flame. Vapors may travel to a source of ignition and flash back. Breathing vapor or spray mist may cause allergic reaction, asthma-like symptoms and lung damage. Persons with respiratory allergies must not work with this product. Avoid contact with skin and eyes.</p>
    <p><b>NIOSH/MSHA</b> approved air-supplied respirator is recommended during spraying. If one is not available, use a properly fitted organic vapor cartridge respirator with particulate prefilter. Ground all equipment. Use explosion-proof ventilation. Dispose of waste and empty containers according to local regulations.</p>
    <h4>First aid:</h4>
    <p>If inhaled, move to fresh air and call a physician if breathing is difficult. On skin contact, wash thoroughly with soap and water. In case of eye contact, flush with water for at least 15 minutes and get medical attention. If swallowed, do not induce vomiting; call a poison control center at once.</p>
    <h4>Notice:</h4>
    <p>Contents are for industrial use only. Product data is believed accurate but is given without warranty. Always test for compatibility before full application.</p>
  </div>

  <div class="company" style="left:543px;top:232px;font-size:5.6px">
    <strong>Halvex Finish, Inc.</strong><br>240 Harlow Park Rd,<br>Ashford, CA 90210<br>(800) 555-0147
    <div style="margin-top:9px"><strong>Made in EU</strong></div>
  </div>
  <div class="liters" style="left:658px;top:283px;font-size:11px">2.5 LITERS</div>

  <div class="reach" style="left:750px;top:238px;width:130px;font-size:5.6px">
    <h5>KEEP OUT OF THE REACH OF CHILDREN</h5>
    <p style="margin-top:8px">Do not store above 30 °C. Keep container tightly closed in a dry, well ventilated place. Contents under no pressure; open slowly.</p>
  </div>
  <div class="danger" style="left:894px;top:240px;width:90px;height:42px">
    <div class="danger__title" style="top:-9px;font-size:15px">DANGER</div>
    <div class="danger__icons" style="top:16px;gap:5px">
      <svg width="20" height="20"><use href="#icon-flame"/></svg>
      <svg width="20" height="20"><use href="#icon-health"/></svg>
      <svg width="20" height="20"><use href="#icon-alert"/></svg>
    </div>
  </div>
</section>
</body>
</html>
```